Tech business card design

We need an amazing business card design for our new business 'Pexla' a marketing tech startup based in Sydney, Australia. We provide an online marketplace for businesses to search and buy advertising media, connect with service providers and learn more about marketing. We wish to communicate 'cool tech', reliability and professionalism and design based around our logo.

Target Market(s)

Business Owners

Contact Information for Business Card

Name
Position
Email Address
Website
Phone Number

Font styles to use
Other font styles liked:
• Avenir & Avenir Next

Colors

Designer to choose colors to be used in the design.

```html
<!DOCTYPE html>
<html lang="en">
<head>
<meta charset="utf-8">
<title>Pexla Business Card</title>
<link href="https://fonts.googleapis.com/css2?family=Nunito+Sans:wght@400;600;800;900&display=swap" rel="stylesheet">
<style>
  :root {
    --backdrop: #1d1e22;
    --navy: #151c48;
    --white: #ffffff;
    --band-grey: #8a8b8f;
    --fold-grey: #5f6064;
    --logo-faint: #5b6188;
    --text-light: #f2f3f8;
  }
  * { margin: 0; padding: 0; box-sizing: border-box; }
  html, body {
    width: 1200px; height: 803px; overflow: hidden;
    background: var(--backdrop);
    font-family: "Nunito Sans", Arial, sans-serif;
  }
  .stage {
    position: relative; width: 1200px; height: 803px;
  }
  .card {
    position: absolute; top: 247px;
    width: 540px; height: 309px;
    overflow: hidden;
    box-shadow: 0 14px 30px rgba(0,0,0,0.55);
  }
  .card-front { left: 40px; background: var(--white); }
  .card-back { left: 620px; background: var(--navy); }
  .front-shapes { position: absolute; inset: 0; }
  .wordmark {
    position: absolute; left: 26px; bottom: 40px;
    font-weight: 900; font-size: 104px; line-height: 1;
    letter-spacing: -3px; color: var(--navy);
  }
  .holder {
    position: absolute; right: 26px; top: 24px;
    text-align: right; color: var(--white);
  }
  .holder-name { font-weight: 800; font-size: 17px; letter-spacing: 0.5px; line-height: 1.1; }
  .holder-role { font-weight: 800; font-size: 12px; line-height: 1.2; }
  .contact {
    position: absolute; right: 26px; top: 108px;
    list-style: none; text-align: right;
    color: var(--text-light); font-size: 13px; line-height: 1.35;
  }
  .contact li { display: flex; justify-content: flex-end; align-items: center; gap: 7px; }
  .contact .address { display: block; margin-bottom: 10px; }
  .contact .gap { margin-top: 8px; }
  .contact svg { width: 12px; height: 12px; flex: none; }
  .back-wordmark {
    position: absolute; left: 0; right: 0; top: 50%;
    transform: translateY(-52%);
    text-align: center;
    font-weight: 900; font-size: 140px; line-height: 1;
    letter-spacing: -4px; color: var(--logo-faint);
  }
</style>
</head>
<body>
<main class="stage">
  <section class="card card-front">
    <svg class="front-shapes" viewBox="0 0 540 309" width="540" height="309" aria-hidden="true">
      <polygon points="250,0 540,0 540,309 330,309" fill="var(--navy)"/>
      <polygon points="250,20 540,20 540,62 262,62" fill="var(--band-grey)"/>
      <polygon points="190,62 318,62 318,90 222,90" fill="var(--fold-grey)"/>
    </svg>
    <div class="wordmark">pexla</div>
    <div class="holder">
      <div class="holder-name">SAM CARTER</div>
      <div class="holder-role">Position</div>
    </div>
    <ul class="contact">
      <li class="address">Street Name, City Name<br>Zipcode:012345</li>
      <li>012-345-6789
        <svg viewBox="0 0 24 24" aria-hidden="true"><path fill="currentColor" d="M6.6 10.8a15.5 15.5 0 0 0 6.6 6.6l2.2-2.2c.3-.3.7-.4 1-.2 1.1.4 2.3.6 3.6.6.6 0 1 .4 1 1V20c0 .6-.4 1-1 1A17 17 0 0 1 3 4c0-.6.4-1 1-1h3.5c.6 0 1 .4 1 1 0 1.3.2 2.5.6 3.6.1.3 0 .7-.2 1z"/></svg>
      </li>
      <li class="gap">info@pexla.com
        <svg viewBox="0 0 24 24" aria-hidden="true"><rect x="2" y="5" width="20" height="14" rx="1" fill="currentColor"/><path d="M2.5 5.5 12 13l9.5-7.5" stroke="var(--navy)" stroke-width="1.6" fill="none"/></svg>
      </li>
      <li class="gap">www.pexla.com
        <svg viewBox="0 0 24 24" aria-hidden="true"><g fill="none" stroke="currentColor" stroke-width="2"><circle cx="12" cy="12" r="9"/><ellipse cx="12" cy="12" rx="4" ry="9"/><path d="M3 12h18"/></g></svg>
      </li>
    </ul>
  </section>
  <section class="card card-back">
    <div class="back-wordmark">pexla</div>
  </section>
</main>
</body>
</html>
```